corvale institute of business and technology web site

I need web site for the institute which focus on business courses and computer course it is also for vocation train for employment It is also carear development and advancement .It should have links to online study resource which free
Industry/Entity Type
Business
Number of Pages Required
1 page
Look and feel
Each slider illustrates characteristics of the customer's brand and the style your logo design should communicate.

```html
<!DOCTYPE html>
<html lang="en">
<head>
<meta charset="utf-8">
<title>Corvale Institute of Business and Technology</title>
<link href="https://fonts.googleapis.com/css2?family=Montserrat:wght@400;600;700;800&family=Open+Sans:wght@400;600;700&family=Lora:ital@1&display=swap" rel="stylesheet">
<style>
:root{
  --green:#6aa82b;
  --green-dark:#4f8a1c;
  --navy:#1d3b72;
  --navy-deep:#142c57;
  --blue:#2a5aa8;
  --ink:#2b2b2b;
  --grey:#777;
  --light:#f2f2f2;
  --white:#fff;
  --orange:#f07b2a;
}
*{box-sizing:border-box;margin:0;padding:0}
html,body{width:1200px;height:3492px;overflow:hidden}
body{font-family:"Open Sans",Arial,sans-serif;color:var(--ink);background:var(--white);position:relative}
.section{position:absolute;left:0;width:1200px}
h1,h2,h3,.nav a,.btn{font-family:"Montserrat",Arial,sans-serif}

/* header */
.site-header{top:0;height:190px;background:var(--white)}
.topbar{position:absolute;right:60px;top:14px;font-size:13px;color:var(--grey);display:flex;gap:26px}
.brand{position:absolute;left:60px;top:28px;display:flex;align-items:center;gap:14px;color:var(--navy);font-family:"Montserrat",Arial,sans-serif;font-weight:700}
.brand-mark{width:70px;height:70px;background:var(--navy);border-radius:8px}
.brand-name{font-size:40px;line-height:1}
.brand-sub{font-size:13px;margin-top:4px;letter-spacing:.3px}
.search{position:absolute;right:60px;top:84px;width:240px;height:32px;border:1px solid #ccc;border-radius:16px;font-size:13px;color:#999;padding:6px 16px}
.nav{position:absolute;right:40px;top:148px;width:560px;height:38px;background:linear-gradient(var(--green),var(--green-dark));display:flex;justify-content:flex-end;align-items:center;gap:34px;padding-right:30px;border-radius:4px 4px 0 0}
.nav a{color:var(--white);text-decoration:none;font-size:14px;font-weight:700}

/* hero */
.hero{top:190px;height:570px;background:linear-gradient(180deg,#eeeeec 0%,#dcdcd8 60%,#c9a97c 100%)}
.hero h1{position:absolute;top:26px;width:100%;text-align:center;font-size:48px;font-weight:700;color:var(--ink)}
.hero-sub{position:absolute;top:176px;width:100%;text-align:center;font-size:30px;color:var(--ink)}
.hero .btn{position:absolute;left:540px;top:455px;width:120px;height:34px;background:#333;color:var(--white);font-size:13px;font-weight:600;text-align:center;line-height:34px}

/* welcome */
.welcome{top:760px;height:580px;text-align:center}
.welcome .eyebrow{margin-top:78px;font-size:16px;color:var(--green);font-weight:700;font-family:"Montserrat",Arial,sans-serif}
.welcome h2{font-size:27px;color:var(--green);font-weight:800;margin-top:2px}
.welcome p{width:960px;margin:20px auto 0;font-size:14px;line-height:22px;color:var(--grey)}
.features{display:flex;justify-content:center;gap:46px;margin-top:60px}
.feature{width:130px}
.feature .disc{width:96px;height:96px;border-radius:50%;background:var(--navy);margin:0 auto;display:flex;align-items:center;justify-content:center;border:4px solid #d8dfec}
.feature .disc.active{background:var(--green);border-color:#d6e8c3}
.feature span{display:block;margin-top:16px;font-size:13px;font-weight:700;line-height:18px;color:var(--ink)}

/* why choose */
.why{top:1340px;height:640px}
.why h2{text-align:center;margin-top:56px;font-size:30px;font-weight:700;color:#3a3a3a;white-space:nowrap}
.points{position:absolute;left:70px;top:130px;width:520px;display:grid;grid-template-columns:1fr 1fr;column-gap:40px;row-gap:34px}
.point .num{font-family:"Montserrat",Arial,sans-serif;font-size:58px;color:#ccc;font-weight:600;line-height:1;float:left;margin-right:10px}
.point h3{font-size:17px;font-weight:700;color:#444;line-height:22px;padding-top:6px}
.point p{clear:both;font-size:12px;line-height:19px;color:var(--grey);padding-top:10px}
.why .photo{position:absolute;left:612px;top:108px;width:588px;height:424px;background:linear-gradient(135deg,#e6e8ea,#aeb3b8 55%,#5a5048)}

/* study banner */
.study{top:1980px;height:340px;background:linear-gradient(180deg,var(--green) 0%,#7cbb38 70%,#b48a55 100%)}
.study .photo{position:absolute;left:0;top:0;width:700px;height:340px;background:linear-gradient(90deg,#f3f3f0 0%,#e2e6da 55%,rgba(124,187,56,0) 100%)}
.study .copy{position:absolute;left:752px;top:64px;width:400px}
.study h2{font-size:46px;font-weight:800;color:var(--white);line-height:50px;white-space:nowrap}
.study .lead{margin-top:4px;font-family:"Montserrat",Arial,sans-serif;font-size:26px;line-height:32px;font-weight:600;color:var(--white);white-space:nowrap}
.study .btn{margin-top:18px;width:220px;height:48px;background:#111;color:var(--white);border-radius:24px;font-size:20px;font-weight:700;text-align:center;line-height:48px}

/* testimonials */
.testimonials{top:2320px;height:528px;text-align:center}
.testimonials h2{margin-top:110px;font-size:32px;font-weight:700;color:#3a3a3a}
.testimonials blockquote{width:900px;margin:36px auto 0;font-family:"Lora",Georgia,serif;font-style:italic;font-size:18px;line-height:30px;color:#555}
.testimonials .arrow{position:absolute;top:230px}
.testimonials .badge{width:28px;height:28px;border-radius:50%;background:var(--orange);margin:44px auto 0}
.testimonials .name{margin-top:16px;font-size:12px;font-weight:700;color:#555}

/* mailing */
.mailing{top:2848px;height:64px;background:var(--green);display:flex;align-items:center;justify-content:center;gap:20px}
.mailing h3{font-size:22px;font-weight:600;color:var(--white);margin-right:10px}
.mailing .field{width:300px;height:36px;background:var(--white);font-size:13px;color:#999;padding:9px 14px}
.mailing .btn{width:140px;height:36px;background:#222;color:var(--white);font-size:13px;font-weight:700;text-align:center;line-height:36px;letter-spacing:1px}

/* footer */
.site-footer{top:2912px;height:508px;background:var(--navy);color:var(--white)}
.site-footer h2{position:absolute;left:70px;top:44px;font-size:24px;font-weight:700}
.contact{position:absolute;left:70px;top:120px;width:320px}
.contact-item{display:flex;gap:22px;margin-bottom:34px}
.contact-item svg{flex:none}
.contact-item h4{font-size:13px;font-weight:700;margin-bottom:6px}
.contact-item p{font-size:13px;line-height:20px;color:#d4dcee}
.message{position:absolute;left:430px;top:120px;width:440px}
.message h4{font-size:13px;font-weight:700;margin-bottom:14px}
.message .row{display:flex;gap:12px}
.message .input{flex:1;height:34px;background:var(--navy-deep);border:1px solid #2f4f8c;font-size:13px;color:#9aa9c8;padding:7px 12px}
.message .area{height:120px;margin-top:12px}
.message .btn{margin-top:14px;width:90px;height:34px;background:var(--blue);text-align:center;line-height:34px;font-size:13px;font-weight:700}
.partner{position:absolute;left:900px;top:120px;width:230px}
.partner h4{font-family:"Montserrat",Arial,sans-serif;font-size:20px;font-weight:800;line-height:24px}
.partner .seal{margin-top:14px;width:180px;height:90px;background:#0d0d0d}
.follow{position:absolute;left:70px;top:452px;display:flex;align-items:center;gap:14px;font-size:13px;font-weight:700}
.pill{width:112px;height:32px;border-radius:16px;font-size:12px;font-weight:600;text-align:center;line-height:32px}
.bottombar{top:3420px;height:72px;background:var(--navy-deep);color:#c9d3e8;font-size:13px}
.bottombar nav{position:absolute;left:70px;top:27px;display:flex;gap:22px;font-weight:700}
.bottombar p{position:absolute;right:70px;top:27px}
</style>
</head>
<body>

<header class="section site-header">
  <div class="topbar"><span>+260 555 014 220</span><span>hello@corvale-edu.example</span></div>
  <div class="brand">
    <div class="brand-mark"></div>
    <div><div class="brand-name">CORVALE</div><div class="brand-sub">INSTITUTE OF BUSINESS &amp; TECHNOLOGY</div></div>
  </div>
  <div class="search">Search</div>
  <nav class="nav"><a href="#">HOME</a><a href="#">ABOUT US</a><a href="#">COURSES</a><a href="#">CONTACT US</a></nav>
</header>

<section class="section hero" role="img" aria-label="Bright study desk with a computer monitor, plant and notebooks against a white brick wall">
  <h1>Lorem ipsum dolor sit amet</h1>
  <div class="hero-sub">Lorem ipsum dolor sit amet, consectetur adipiscing elit</div>
  <div class="btn">LEARN MORE</div>
</section>

<section class="section welcome">
  <div class="eyebrow">WELCOME TO</div>
  <h2>CORVALE INSTITUTE OF BUSINESS AND TECHNOLOGY</h2>
  <p>Lorem ipsum dolor sit amet, consectetur adipiscing elit, sed diam nonummy nibh euismod tincidunt ut laoreet dolore magna aliquam erat volutpat. Ut wisi enim ad minim veniam, quis nostrud exerci tation ullamcorper suscipit lobortis nisl ut aliquip ex ea commodo consequat. Duis autem vel eum iriure dolor in hendrerit in vulputate velit esse molestie consequat.</p>
  <div class="features">
    <div class="feature"><div class="disc"></div><span>University Education - Long Distance Learning</span></div>
    <div class="feature"><div class="disc"></div><span>Modular Soft Skills</span></div>
    <div class="feature"><div class="disc active"></div><span>Direct to Device (D2D)</span></div>
    <div class="feature"><div class="disc"></div><span>Brightpath</span></div>
    <div class="feature"><div class="disc"></div><span>Brightpath Online In The Talent Continuum</span></div>
    <div class="feature"><div class="disc"></div><span>Business Verticals</span></div>
  </div>
</section>

<section class="section why">
  <h2>WHY CHOOSE CORVALE INSTITUTE OF BUSINESS AND TECHNOLOGY</h2>
  <div class="points">
    <div class="point"><div class="num">01</div><h3>Over 50 years of experience</h3><p>Duis autem vel eum iriure dolor in hendrerit in vulputate velit esse molestie consequat, vel illum dolore eu feugiat nulla facilisis.</p></div>
    <div class="point"><div class="num">02</div><h3>We are passionate</h3><p>Duis autem vel eum iriure dolor in hendrerit in vulputate velit esse molestie consequat, vel illum dolore eu feugiat nulla facilisis.</p></div>
    <div class="point"><div class="num">03</div><h3>We are fast, accuracy &amp; reliable</h3><p>Duis autem vel eum iriure dolor in hendrerit in vulputate velit esse molestie consequat, vel illum dolore eu feugiat nulla facilisis.</p></div>
    <div class="point"><div class="num">04</div><h3>We are improving everyday</h3><p>Duis autem vel eum iriure dolor in hendrerit in vulputate velit esse molestie consequat, vel illum dolore eu feugiat nulla facilisis.</p></div>
  </div>
  <div class="photo" role="img" aria-label="Smiling student standing in a modern open-plan office"></div>
</section>

<section class="section study">
  <div class="photo" role="img" aria-label="Young woman lying on the floor studying on a laptop"></div>
  <div class="copy">
    <h2>ONLINE STUDY</h2>
    <div class="lead">RESOURCE WHICH FREE</div>
    <div class="btn">CLICK HERE</div>
  </div>
</section>

<section class="section testimonials">
  <h2>CLIENT'S TESTIMONIALS</h2>
  <svg class="arrow" style="left:60px" width="24" height="48" viewBox="0 0 24 48"><polyline points="20,2 4,24 20,46" fill="none" stroke="#bbb" stroke-width="2"/></svg>
  <svg class="arrow" style="right:60px" width="24" height="48" viewBox="0 0 24 48"><polyline points="4,2 20,24 4,46" fill="none" stroke="#bbb" stroke-width="2"/></svg>
  <blockquote>Lorem ipsum dolor sit amet, consectetur adipiscing elit, sed do eiusmod tempor incididunt ut labore et dolore magna aliqua. Ut enim ad minim veniam, quis nostrud exercitation ullamco laboris nisi ut aliquip ex ea commodo consequat.</blockquote>
  <div class="badge"></div>
  <div class="name">DANIEL OKORO</div>
</section>

<section class="section mailing">
  <h3>JOIN OUR MAILING LIST</h3>
  <div class="field">Sign up to our mailing list</div>
  <div class="btn">SUBSCRIBE</div>
</section>

<footer class="section site-footer">
  <h2>GET IN TOUCH NOW!</h2>
  <div class="contact">
    <div class="contact-item">
      <svg width="26" height="32" viewBox="0 0 26 32"><path d="M13 1a11 11 0 0 1 11 11c0 8-11 19-11 19S2 20 2 12A11 11 0 0 1 13 1z" fill="#fff"/><circle cx="13" cy="12" r="4" fill="#1d3b72"/></svg>
      <div><h4>ADDRESS</h4><p>14 Kestrel Court, Maple Row<br>Plot 22, Maple Row</p></div>
    </div>
    <div class="contact-item">
      <svg width="26" height="26" viewBox="0 0 26 26"><path d="M6 2l5 5-3 4c2 3 4 5 7 7l4-3 5 5-4 4C10 24 2 16 2 6z" fill="#fff"/></svg>
      <div><h4>PHONE</h4><p>+260 555 014 220, +260 555 014 221</p></div>
    </div>
    <div class="contact-item">
      <svg width="26" height="20" viewBox="0 0 26 20"><rect x="1" y="1" width="24" height="18" fill="#fff"/><polyline points="1,1 13,11 25,1" fill="none" stroke="#1d3b72" stroke-width="2"/></svg>
      <div><h4>EMAIL</h4><p>hello@corvale-edu.example</p></div>
    </div>
  </div>
  <div class="message">
    <h4>LEAVE A MESSAGE</h4>
    <div class="row"><div class="input">Name</div><div class="input">Email</div></div>
    <div class="input area">Message</div>
    <div class="btn">SUBMIT</div>
  </div>
  <div class="partner">
    <h4>IN CONJUNCTION WITH BRIGHTPATH</h4>
    <div class="seal"></div>
  </div>
  <div class="follow">
    <span>FOLLOW US</span>
    <div class="pill" style="background:#3b5a9a">Friendwall</div>
    <div class="pill" style="background:#3fa9e0">Chirply</div>
    <div class="pill" style="background:#d24a36">Circlo</div>
    <div class="pill" style="background:#c8232c">Pinboardly</div>
    <div class="pill" style="background:#1b75b0">Linkwork</div>
  </div>
</footer>

<div class="section bottombar">
  <nav><span>HOME</span><span>ABOUT US</span><span>COURSES</span><span>CONTACT US</span></nav>
  <p>© 2015 Corvale Institute Of Business And Technology. All Rights Reserved.</p>
</div>

</body>
</html>
```